Elegant Business Card for Technology Company

Client is a supplier of innovative industrial communications and automation equipment since 2002. This contest is to gather fresh ideas for a redesign of the existing business card. Client is looking for design that best communicates tagline "Industrial Networking and Computing Specialist".

Design submissions should look modern, clean, elegant and professional. It should not be cluttered. Use white as the primary colour. Orange and black as secondary colour. Refer to jpeg File 1 on the current design.

Fonts used by Client used include Arial Regular, Arial Black, Roboto Regular, Roboto Black and Lato.

The winning design will be sent for offset printing using super white 250gsm artcard paper (open for suggestions).

Target Market(s)

System Engineers, Project Managers, Purchasing Managers from companies providing engineering services for Smart Cities.

Industry/Entity Type

Information Technology

Contact Information for Business Card

Refer to PDF File 3 for Business Card Details. Priority of short contact information would be as follows Name > Job Title > Email > Mobile > Web > Tel > Fax > Business Address >UEN (UEN represents company registration number)

Font styles to use
Sans Serif

Colors
ffffff
f37122
000000
5c5c5c

Requirements
Must have
• Refer to AI File 2 (Company Logo) & PDF File 3 (Information on Namecard)
Should not have
• No QR codes
• No Social Media Icons
• Do not create full Black or Orange colour background

```html
<!DOCTYPE html>
<html lang="en">
<head>
<meta charset="utf-8">
<title>ORV Business Card</title>
<link rel="stylesheet" href="https://fonts.googleapis.com/css2?family=Open+Sans:wght@400;700&display=swap">
<style>
  :root {
    --paper: #ffffff;
    --orange: #f37122;
    --ink: #000000;
    --grey: #5c5c5c;
    --backdrop: #ececec;
    --tint: #fdeee3;
  }
  * { box-sizing: border-box; margin: 0; padding: 0; }
  html, body { width: 1105px; height: 1200px; overflow: hidden; }
  body {
    background: var(--backdrop);
    font-family: "Open Sans", Arial, sans-serif;
    position: relative;
  }
  .card {
    position: absolute;
    left: 180px;
    width: 746px;
    height: 427px;
    background: var(--paper);
    overflow: hidden;
  }
  .card--front { top: 118px; }
  .card--back { top: 636px; }

  /* front */
  .edge-band {
    position: absolute; left: 0; top: 0; bottom: 0;
    width: 52px; background: var(--orange);
  }
  .edge-rule {
    position: absolute; left: 55px; top: 0; bottom: 0;
    width: 4px; background: var(--ink);
  }
  .brand { position: absolute; }
  .brand__name {
    display: block;
    font-weight: 700;
    color: var(--ink);
    line-height: 1;
  }
  .card--front .brand { left: 72px; top: 66px; }
  .card--front .brand__name { font-size: 90px; letter-spacing: 4px; }

  .contact-list {
    position: absolute; left: 106px; top: 244px;
    list-style: none;
    font-size: 19px; color: var(--grey);
  }
  .contact-list li {
    display: flex; align-items: center; gap: 10px;
    height: 28.5px;
  }
  .contact-list svg { width: 17px; height: 17px; fill: var(--orange); flex: none; }

  .person {
    position: absolute; right: 41px; top: 240px;
    text-align: right;
  }
  .person__name { font-size: 26px; color: var(--orange); line-height: 34px; }
  .person__title { font-size: 20px; color: var(--ink); line-height: 28px; margin-bottom: 2px; }
  .person__address { font-style: normal; font-size: 19px; color: var(--grey); line-height: 28px; }

  /* back */
  .back-pattern {
    position: absolute; inset: 0;
    background: linear-gradient(135deg, var(--tint) 0%, var(--paper) 40%, var(--paper) 60%, var(--tint) 100%);
  }
  .card--back .brand {
    left: 0; right: 0; top: 111px;
    text-align: center;
  }
  .card--back .brand__name { font-size: 120px; letter-spacing: 6px; }
  .tagline {
    position: absolute; left: 0; right: 0; top: 290px;
    text-align: center;
    font-size: 20px; line-height: 26.5px; color: var(--grey);
  }
</style>
</head>
<body>

<section class="card card--front" aria-label="Business card front">
  <div class="edge-band"></div>
  <div class="edge-rule"></div>

  <div class="brand">
    <span class="brand__name">ORV</span>
  </div>

  <ul class="contact-list">
    <li>
      <svg viewBox="0 0 16 16" aria-hidden="true"><path d="M3.5 1 6 3.5 4.7 5.6c.9 2 2.5 3.6 4.6 4.6L11.4 9 14 11.5 12.6 14C7 14 2 9 2 3.4Z"/></svg>
      <span>+65 6200 1450</span>
    </li>
    <li>
      <svg viewBox="0 0 16 16" aria-hidden="true"><path d="M4.5 1h7a1 1 0 0 1 1 1v12a1 1 0 0 1-1 1h-7a1 1 0 0 1-1-1V2a1 1 0 0 1 1-1Zm.8 2v9h5.4V3ZM8 12.6a.8.8 0 1 0 0 1.6.8.8 0 0 0 0-1.6Z"/></svg>
      <span>+65 9123 4567</span>
    </li>
    <li>
      <svg viewBox="0 0 16 16" aria-hidden="true"><path d="M4 1h8v4H4Zm-2 5h12a1 1 0 0 1 1 1v5h-2v3H3v-3H1V7a1 1 0 0 1 1-1Zm3 5v2.5h6V11Z"/></svg>
      <span>+65 6200 1451</span>
    </li>
    <li>
      <svg viewBox="0 0 16 16" aria-hidden="true"><path d="M1 3h14v1.2L8 8.8 1 4.2Zm0 2.6 7 4.6 7-4.6V13H1Z"/></svg>
      <span>sales@orvnet.com.sg</span>
    </li>
    <li>
      <svg viewBox="0 0 16 16" aria-hidden="true"><path d="M8 1a7 7 0 1 0 0 14A7 7 0 0 0 8 1Zm-1 2.2v2L5 7 3.3 6.5A5 5 0 0 1 7 3.2Zm2 .1a5 5 0 0 1 3.6 7.2L11 9.5V8L9 7V5.5l1.5-1Zm-5.7 5L5 9l1 2v2.4a5 5 0 0 1-2.7-5.1Z"/></svg>
      <span>www.orvnet.com.sg</span>
    </li>
  </ul>

  <div class="person">
    <p class="person__name">Daniel Lim</p>
    <p class="person__title">Sales Manager</p>
    <address class="person__address">
      24 Kallang Way<br>
      Innopark #05-12 (Block B)<br>
      Singapore 349410
    </address>
  </div>
</section>

<section class="card card--back" aria-label="Business card back">
  <div class="back-pattern" role="img" aria-label="Faint pale orange decorative background pattern"></div>

  <div class="brand">
    <span class="brand__name">ORV</span>
  </div>

  <p class="tagline">
    Industrial Networking &amp; Computing Specialist<br>
    Industrial Ethernet / Wireless / Cellular<br>
    Industrial &amp; Embedded Computing / Serial / Fieldbus Connectivity<br>
    IP Video Surveillance / Remote Automation
  </p>
</section>

</body>
</html>
```